business card - Helicopter Flight Services, Flight School, etc.

We need a business card design for a new helicopter service.

We offer Helicopter Flight Services, Aerial Filming & Photography, Flight School, and Helicopter Tours. In that order.

Summit BladeAir, Inc.
Dennis Tollerby
SummitBladeair@Kestmail.com
626-418-7352

Based at the Brenwick Airport in Van Nuys, CA. The final design should communicate integrity and safety. Pictures or logos at your discretion.

Card back side - surprise me.

```html
<!DOCTYPE html>
<html lang="en">
<head>
<meta charset="utf-8">
<title>Summit BladeAir, Inc. – Business Card</title>
<link href="https://fonts.googleapis.com/css2?family=Open+Sans:wght@400;600&display=swap" rel="stylesheet">
<style>
  :root {
    --page-bg: #e6e3de;
    --card-white: #fbfbfb;
    --card-black: #0b0b0b;
    --brand-blue: #3d3cb0;
    --ink: #1a1a1a;
    --white: #f4f4f4;
  }
  * { margin: 0; padding: 0; box-sizing: border-box; }
  html, body {
    width: 1200px; height: 892px; overflow: hidden;
    background: var(--page-bg);
    font-family: "Open Sans", Arial, sans-serif;
  }
  .canvas {
    position: relative; width: 1200px; height: 892px;
    display: flex; align-items: center; justify-content: center; gap: 50px;
  }
  .card {
    position: relative; width: 540px; height: 309px;
    box-shadow: 0 10px 28px rgba(0,0,0,0.22);
    overflow: hidden;
  }
  .card-front {
    background: linear-gradient(160deg, #ffffff 0%, var(--card-white) 55%, #ededed 100%);
  }
  .company-name {
    position: absolute; left: 30px; top: 30px;
    font-size: 27px; font-weight: 400; color: var(--brand-blue);
    letter-spacing: 0.2px;
  }
  .divider {
    position: absolute; left: 292px; top: 92px; width: 6px; height: 200px;
  }
  .contact-block {
    position: absolute; left: 318px; top: 108px;
  }
  .person-name {
    font-size: 23px; color: var(--brand-blue); margin-bottom: 12px;
  }
  .contact-list { list-style: none; }
  .contact-list li {
    display: flex; align-items: center; gap: 8px;
    font-size: 12.5px; color: var(--ink); line-height: 21px;
  }
  .contact-list .icon {
    width: 12px; height: 12px; flex: none;
    background: var(--brand-blue); display: flex; align-items: center; justify-content: center;
  }
  .contact-list .no-icon { width: 12px; flex: none; }
  .card-back {
    background: linear-gradient(150deg, #1c1c1c 0%, var(--card-black) 45%, #000 100%);
    display: flex; flex-direction: column; align-items: center; justify-content: center;
    color: var(--white);
  }
  .back-name { font-size: 40px; font-weight: 400; letter-spacing: 0.5px; }
  .back-tagline { font-size: 15px; margin-top: 8px; letter-spacing: 0.3px; }
</style>
</head>
<body>
<main class="canvas">
  <section class="card card-front" aria-label="Card front">
    <h1 class="company-name">Summit BladeAir, Inc.</h1>
    <svg class="divider" viewBox="0 0 6 200" aria-hidden="true">
      <polygon points="3,0 5,100 3,200 1,100" fill="#111"/>
    </svg>
    <div class="contact-block">
      <h2 class="person-name">Dennis Tollerby</h2>
      <ul class="contact-list">
        <li><span class="icon"><svg width="8" height="8" viewBox="0 0 8 8"><path d="M1 1.5 C1 5 3 7 6.5 7 L7 5.5 5.5 4.8 4.8 5.6 C3.6 5 3 4.4 2.4 3.2 L3.2 2.5 2.5 1 Z" fill="#fff"/></svg></span>626-418-7352</li>
        <li><span class="icon"><svg width="8" height="8" viewBox="0 0 8 8"><rect x="0.5" y="1.5" width="7" height="5" fill="none" stroke="#fff" stroke-width="1"/><path d="M0.5 1.8 L4 4.5 7.5 1.8" fill="none" stroke="#fff" stroke-width="1"/></svg></span>SummitBladeair@Kestmail.com</li>
        <li><span class="icon"><svg width="8" height="8" viewBox="0 0 8 8"><path d="M4 0.8 L7.4 4 H6.3 V7.2 H1.7 V4 H0.6 Z" fill="#fff"/></svg></span>2270 W. Larkfield Ave. Ste.B</li>
        <li><span class="no-icon"></span>Halden, CA 91802</li>
      </ul>
    </div>
  </section>
  <section class="card card-back" aria-label="Card back">
    <p class="back-name">Summit BladeAir, Inc.</p>
    <p class="back-tagline">Brenwick Airport · Tour guide · Heliport</p>
  </section>
</main>
</body>
</html>
```